Lo Mara Menu Design Project

This project is pretty straight forward. You will be given 3 files which include the following:
1. Our proposed menu
2. Our Company logo
3. A sample menu on what we are looking for design wise

Your job is to create a visually pleasing menu that is simple, clean and fresh. Please refer to our home website for additional information. (www.lomara-eats.com) Must be in eps or equivalent format.

Target Market(s)

20s to 40s

Industry/Entity Type

It Company

Requirements
Must have
• Company log
Must be in EPS format

```html
<!DOCTYPE html>
<html lang="en">
<head>
<meta charset="utf-8">
<title>Lo Mara — Beef &amp; Pork / Seafood Menu</title>
<link href="https://fonts.googleapis.com/css2?family=Josefin+Sans:ital,wght@0,400;0,600;0,700;1,300;1,600&display=swap" rel="stylesheet">
<style>
  :root {
    --bg-deep: #0b0706;
    --bg-warm: #3a1a10;
    --bg-ember: #6a2c16;
    --accent-red: #d8282c;
    --text-white: #ffffff;
    --text-soft: #e9e4e2;
  }
  * { box-sizing: border-box; margin: 0; padding: 0; }
  html, body { width: 1200px; height: 1000px; overflow: hidden; background: var(--bg-deep); }
  .menu {
    position: relative; width: 1200px; height: 1000px; overflow: hidden;
    font-family: "Josefin Sans", sans-serif; color: var(--text-white);
  }
  .menu__backdrop {
    position: absolute; inset: 0;
    background:
      radial-gradient(ellipse 420px 360px at 300px 520px, rgba(120,48,22,.55), transparent 70%),
      radial-gradient(ellipse 520px 420px at 820px 430px, rgba(110,44,20,.55), transparent 70%),
      radial-gradient(ellipse 300px 260px at 1030px 760px, rgba(150,120,100,.25), transparent 70%),
      linear-gradient(180deg, var(--bg-deep) 0%, var(--bg-warm) 45%, #24110b 80%, var(--bg-deep) 100%);
  }
  .menu__divider {
    position: absolute; left: 601px; top: 0; width: 3px; height: 1000px; background: #8e1a1c;
  }
  .section { position: absolute; top: 22px; }
  .section--beef { left: 50px; width: 505px; }
  .section--seafood { left: 655px; width: 493px; }
  .section__title {
    color: var(--accent-red); text-align: center; font-weight: 600;
    font-size: 29px; letter-spacing: 1px; line-height: 34px; margin-bottom: 10px;
  }
  .section__notes {
    text-align: center; font-style: italic; font-weight: 300;
    font-size: 19px; line-height: 25px; color: var(--text-soft); margin-bottom: 18px;
  }
  .dish { font-size: 18px; line-height: 25px; }
  .dish__head { display: flex; justify-content: space-between; font-weight: 600; }
  .dish__price { padding-right: 2px; }
  .dish__desc {
    text-align: right; font-style: italic; font-weight: 300; color: var(--text-soft);
  }
  .dish__desc--featured { font-weight: 600; color: var(--text-white); }
  .brand {
    position: absolute; display: flex; align-items: center; gap: 5px;
    font-weight: 700; font-size: 15px; color: var(--accent-red); line-height: 1;
  }
  .brand__mark { width: 9px; height: 9px; background: var(--accent-red); }
  .brand--left { left: 20px; bottom: 38px; }
  .brand--right { left: 1128px; bottom: 38px; }
</style>
</head>
<body>
<main class="menu">
  <div class="menu__backdrop" role="img" aria-label="Dark close-up photo of a plate of glazed crispy shrimp over white rice with chopsticks"></div>
  <div class="menu__divider"></div>

  <section class="section section--beef">
    <h2 class="section__title">BEEF &amp; PORK</h2>
    <p class="section__notes">Rice is not included. Add rice $1.25.<br>Enjoy a Half Chinese Chicken Salad or Plain Fried<br>Rice with any entrée for $5.50<br>Can replace Beef/Pork with Tofu for $1.50</p>

    <div class="dish"><div class="dish__head"><span>Mongolian Beef</span><span class="dish__price">12.25</span></div>
      <p class="dish__desc">Flank steak, garlic, ginger, and green onions on a<br>bed of white crunchies.</p></div>
    <div class="dish"><div class="dish__head"><span>Beef And Broccoli</span><span class="dish__price">11.95</span></div>
      <p class="dish__desc">Flank steak, broccoli, and black mushrooms sautéed<br>in a garlic brown sauce.</p></div>
    <div class="dish"><div class="dish__head"><span>Pepper Steak</span><span class="dish__price">11.95</span></div>
      <p class="dish__desc">Flank steak, bell peppers, onions, and garlic in black<br>pepper sauce.</p></div>
    <div class="dish"><div class="dish__head"><span>Sliced Barbequed Pork</span><span class="dish__price">8.95</span></div>
      <p class="dish__desc dish__desc--featured">Tender slices of juicy pork topped with scallions<br>in a barbeque sauce.</p></div>
    <div class="dish"><div class="dish__head"><span>Barbequed Spareribs</span><span class="dish__price">8.95</span></div>
      <p class="dish__desc">Slow-Roasted juicy pork ribs with barbeque sauce.</p></div>
    <div class="dish"><div class="dish__head"><span>Tangerine Beef</span><span class="dish__price">12.25</span></div>
      <p class="dish__desc">Crisp flank steak topped with scallions in a tangerine<br>sauce.</p></div>
    <div class="dish"><div class="dish__head"><span>Spicy Garlic Tomato Beef</span><span class="dish__price">12.95</span></div>
      <p class="dish__desc">Flank steak, tomato, water chestnuts, zucchini, onions,<br>and spicy garlic sauce.</p></div>
    <div class="dish"><div class="dish__head"><span>Ma Pao Tofu</span><span class="dish__price">7.95</span></div>
      <p class="dish__desc">Soft tofu cubes with ground pork or chicken cooked<br>in Szechuan-Style sauce.</p></div>
  </section>

  <section class="section section--seafood">
    <h2 class="section__title">SEAFOOD</h2>
    <p class="section__notes">Enjoy a Half Chinese Chicken Salad or Plain Fried<br>Rice with any entrée for $5.50<br>Can replace Seafood with Tofu for $1.50</p>

    <div class="dish"><div class="dish__head"><span>Crispy Spicy Honey Shrimp</span><span class="dish__price">13.95</span></div>
      <p class="dish__desc">Crispy large shrimp with red bell peppers, scallions,<br>and chili peppers in a sweet honey sauce.</p></div>
    <div class="dish"><div class="dish__head"><span>Kung Pao Three Treasures</span><span class="dish__price">13.95</span></div>
      <p class="dish__desc">Large shrimp, beef, and chicken breast with scal-<br>lions, peanuts, water chestnuts, and chili peppers.<br>Prepared mandarin-Style.</p></div>
    <div class="dish"><div class="dish__head"><span>Honey Walnut Shrimp</span><span class="dish__price">13.95</span></div>
      <p class="dish__desc">Lightly crisped savory shrimp with honey-Glazed<br>walnuts.</p></div>
    <div class="dish"><div class="dish__head"><span>Fish With Ginger Soy Sauce</span><span class="dish__price">15.95</span></div>
      <p class="dish__desc">Whole white fish filet steamed with ginger and<br>topped with green onions and cilantro.</p></div>
    <div class="dish"><div class="dish__head"><span>Shrimp With Snow Peas</span><span class="dish__price">13.95</span></div>
      <p class="dish__desc">Large shrimp with snow peas, water chestnuts,<br>carrots, and ginger in a white wine sauce.</p></div>
    <div class="dish"><div class="dish__head"><span>Shrimp With Lobster Sauce</span><span class="dish__price">13.95</span></div>
      <p class="dish__desc">Large shrimp, eggs, ground pork, snow peas, water<br>chestnuts, and red bell peppers sautéed in a lob-<br>ster sauce.</p></div>
    <div class="dish"><div class="dish__head"><span>Salt And Pepper Shrimp</span><span class="dish__price">13.95</span></div>
      <p class="dish__desc">Lightly battered large shrimp with a pepper spice;<br>served with bell peppers and white crunchies.</p></div>
    <div class="dish"><div class="dish__head"><span>Cashew Shrimp</span><span class="dish__price">13.95</span></div>
      <p class="dish__desc">Large shrimp with zucchini, onions, and roasted ca-<br>shews in oyster sauce.</p></div>
    <div class="dish"><div class="dish__head"><span>Orange Shrimp</span><span class="dish__price">13.95</span></div>
      <p class="dish__desc">Large crispy shrimp with onions and red and green<br>bell peppers in a sweet orange sauce.</p></div>
  </section>

  <div class="brand brand--left"><span class="brand__mark"></span><span>Lo Mara</span></div>
  <div class="brand brand--right"><span class="brand__mark"></span><span>Lo Mara</span></div>
</main>
</body>
</html>
```